Business Cards Needed for Innovative Healthcare Marketing Company

We are a marketing company focused on healthcare. Our company is all about rebranding yourself renewing your image and generating results. The phoenix stands for "reborn" or "rising" which we provide new brands for our clients we take their old brands and renew it with creativity and innovation. I am looking for a business card with color dimension. I have attached an example of a card I think has the look and feel of what I am trying to accomplish. I like that the card example has black and grey font colors, I like the font placement and the small logo, I really like the use of the colors on the right those are the colors of my logo. My logo is phoenix so maybe incorporating flames similar to that design. I would like the back a solid color maybe red with an opaque version of the logo and website. As a marketing company I am always open to creative liberty!

Target Market(s)

Doctors and business professionals.

Industry/Entity Type

Marketing

Contact Information for Business Card

Valcorne Health Care Marketing
Marla Tenwick- CEO
#(512)638-2974
email-marla@valcorne.com
website- valcorne.com

Font styles to use
Sans Serif

Colors
ec1f27
f37122
ffc214
fbed22
fbf289
f04a50

Requirements
Must have
• The logo and required information
Nice to have
• icons by the information
Should not have
• child like font

```html
<!DOCTYPE html>
<html lang="en">
<head>
<meta charset="utf-8">
<title>Valcorne Health Care Marketing – Business Card</title>
<link rel="stylesheet" href="https://fonts.googleapis.com/css2?family=Open+Sans:wght@400;600;700&family=Quicksand:wght@400&display=swap">
<style>
  :root {
    --canvas-bg: #ece9e6;
    --card-white: #ffffff;
    --brand-red: #9e2520;
    --band-top: #f39a24;
    --band-mid: #e06a1f;
    --band-bottom: #a8271f;
    --back-left: #ee8a26;
    --back-right: #a6261f;
    --mark-grey: #bdbdbd;
    --text-light: #ffffff;
  }
  * { margin: 0; padding: 0; box-sizing: border-box; }
  html, body { width: 1200px; height: 900px; overflow: hidden; }
  body {
    background: var(--canvas-bg);
    font-family: "Open Sans", Arial, sans-serif;
    position: relative;
  }
  .card {
    position: absolute;
    overflow: hidden;
    box-shadow: 0 6px 18px rgba(0,0,0,0.18);
  }

  /* Front */
  .card-front {
    left: 78px; top: 33px; width: 588px; height: 364px;
    background: var(--card-white);
  }
  .brand-lockup {
    position: absolute; left: 32px; top: 48px;
    display: flex; align-items: center; gap: 16px;
  }
  .brand-dot {
    width: 64px; height: 64px; border-radius: 50%;
    background: var(--brand-red);
  }
  .brand-name {
    font-family: "Quicksand", "Open Sans", sans-serif;
    font-weight: 400;
    color: var(--brand-red);
    line-height: 1;
  }
  .brand-name .word { display: block; font-size: 48px; letter-spacing: 1px; }
  .brand-name .tagline { display: block; font-size: 17px; letter-spacing: 1.4px; margin-top: 10px; }

  .contact-band {
    position: absolute; left: 0; top: 189px; width: 100%; height: 175px;
    background: linear-gradient(180deg, var(--band-top) 0%, var(--band-mid) 50%, var(--band-bottom) 100%);
  }
  .contact-block {
    position: absolute; left: 30px; top: 203px; color: var(--text-light);
  }
  .person-name { font-size: 20px; font-weight: 700; line-height: 1.2; }
  .person-role { font-size: 14px; margin-top: 3px; }
  .contact-list { list-style: none; margin-top: 18px; }
  .contact-list li {
    display: flex; align-items: center; gap: 7px;
    font-size: 15px; line-height: 24.5px;
  }
  .contact-list svg { width: 12px; height: 12px; fill: var(--text-light); flex: none; }

  .mark-panel {
    position: absolute; left: 372px; top: 192px; width: 230px; height: 190px;
    background: var(--card-white);
    border-radius: 48px 0 0 0;
  }
  .mark-decoration {
    position: absolute; left: 392px; top: 200px; width: 138px; height: 138px;
    border-radius: 50%;
    background: var(--mark-grey);
  }

  /* Back */
  .card-back {
    left: 389px; top: 505px; width: 565px; height: 352px;
    background: linear-gradient(100deg, var(--back-left) 0%, #d9591f 55%, var(--back-right) 100%);
  }
  .back-decoration {
    position: absolute; left: 140px; top: 10px; width: 300px; height: 300px;
    border-radius: 50%;
    background: radial-gradient(circle, rgba(246,150,40,0.55), rgba(180,40,30,0.25) 70%, rgba(180,40,30,0) 100%);
  }
  .back-website {
    position: absolute; left: 0; right: 0; top: 287px;
    text-align: center;
    color: var(--text-light);
    font-size: 14px; font-weight: 600;
    letter-spacing: 4.6px;
  }
</style>
</head>
<body>

  <section class="card card-front" aria-label="Business card front">
    <div class="brand-lockup">
      <span class="brand-dot"></span>
      <span class="brand-name">
        <span class="word">VALCORNE</span>
        <span class="tagline">HEALTH CARE MARKETING</span>
      </span>
    </div>

    <div class="contact-band"></div>

    <div class="contact-block">
      <p class="person-name">Marla Tenwick</p>
      <p class="person-role">CEO</p>
      <ul class="contact-list">
        <li>
          <svg viewBox="0 0 24 24" aria-hidden="true"><path d="M6.6 10.8a15.1 15.1 0 0 0 6.6 6.6l2.2-2.2a1 1 0 0 1 1-.25 11.4 11.4 0 0 0 3.6.57 1 1 0 0 1 1 1V20a1 1 0 0 1-1 1A17 17 0 0 1 3 4a1 1 0 0 1 1-1h3.5a1 1 0 0 1 1 1c0 1.25.2 2.45.57 3.57a1 1 0 0 1-.25 1z"/></svg>
          (512)638-2974
        </li>
        <li>
          <svg viewBox="0 0 24 24" aria-hidden="true"><path d="M2 5h20v14H2z M2 5l10 8 10-8" fill="none" stroke="#fff" stroke-width="0"/><path d="M2 5h20v2l-10 7L2 7z M2 9l10 7 10-7v10H2z"/></svg>
          marla@valcorne.com
        </li>
        <li>
          <svg viewBox="0 0 24 24" aria-hidden="true"><circle cx="12" cy="12" r="10"/></svg>
          www.valcorne.com
        </li>
      </ul>
    </div>

    <div class="mark-panel"></div>
    <div class="mark-decoration" role="img" aria-label="Large grey brand emblem area"></div>
  </section>

  <section class="card card-back" aria-label="Business card back">
    <div class="back-decoration" role="img" aria-label="Faint tone-on-tone brand emblem area"></div>
    <p class="back-website">www.valcorne.com</p>
  </section>

</body>
</html>
```